High Tech Real Estate Startup needs a business card

We are developing an innovative real estate marketing product based around advanced search and virtual reality.

We talk to people, we need business cards.

Target Market(s)

The target market is technology professionals and realtors.

Contact Information for Business Card

The information to be included will include

Name
Title
Phone Number
E-mail Address
www.zelquin.com

It should use simple iconography for each one of those fields.

Font styles to use
Other font styles liked:
• Co, Jubilat, Avenir

Colors

Designer to choose colors to be used in the design.

Requirements
Must have
• Clean aesthetic,
• Good use of negative space.
• It should use our company logo, shown in the attached file. It is able to use the negative of that logo (coloured font and white background) and I have attached other acceptable accent colours in a swatch file.
Should not have
• Should not be too busy
• No extraneous text (slogans, tag lines etc)

```html
<!DOCTYPE html>
<html lang="en">
<head>
<meta charset="utf-8">
<title>Zelquin Business Card</title>
<link rel="stylesheet" href="https://fonts.googleapis.com/css2?family=Montserrat:wght@400;500;600;700&display=swap">
<style>
  :root {
    --backdrop: #1f1f1f;
    --brand-teal: #00b9bc;
    --card-white: #f4f4f4;
    --ink-grey: #6e6e6e;
    --ink-soft: #7a7a7a;
  }
  html, body {
    margin: 0;
    padding: 0;
    overflow: hidden;
  }
  body {
    width: 1200px;
    height: 960px;
    background: var(--backdrop);
    position: relative;
    font-family: "Montserrat", sans-serif;
  }
  .card {
    position: absolute;
    left: 320px;
    width: 600px;
    box-sizing: border-box;
  }
  .card-front {
    top: 106px;
    height: 344px;
    background: var(--brand-teal);
    display: flex;
    align-items: center;
    justify-content: center;
  }
  .brand-name {
    margin: 0;
    color: #ffffff;
    font-weight: 500;
    font-size: 78px;
    letter-spacing: 2px;
    line-height: 1;
    transform: translateY(-3px);
  }
  .card-back {
    top: 493px;
    height: 342px;
    background: var(--card-white);
    text-align: center;
    padding-top: 126px;
  }
  .contact-name {
    margin: 0;
    color: var(--brand-teal);
    font-weight: 600;
    font-size: 21px;
    line-height: 26px;
  }
  .contact-title {
    margin: 0 0 10px;
    color: var(--ink-grey);
    font-weight: 700;
    font-size: 14px;
    line-height: 20px;
  }
  .contact-line {
    margin: 0;
    color: var(--ink-soft);
    font-weight: 400;
    font-size: 14px;
    line-height: 20px;
  }
  .contact-web {
    letter-spacing: 3px;
  }
</style>
</head>
<body>
  <section class="card card-front">
    <h1 class="brand-name">ZELQUIN</h1>
  </section>
  <section class="card card-back">
    <p class="contact-name">DARA WHITLOW</p>
    <p class="contact-title">CEO/Founder</p>
    <p class="contact-line">555 014 7720 | dara@zelquin.com</p>
    <p class="contact-line contact-web">www.zelquin.com</p>
  </section>
</body>
</html>
```